Business cards for 3 Realtors at one brokerage

We will need a business card template that can be projected on 3 business cards. Harborline Realty & Investment Corp. has 3 realtors on staff Dane, Owen, and Miles. We all want a business card that shows our new logo and information. I will attach many versions of our Logo as well as head shots for each realtor (Owen- Long hair, youngest. Miles- Suit jacket, parted hair cut. Dane- Angled Pose, Shirt and Tie.) I have attached our information below.

Dane Foskett
801-555-0147
dane@harborlinehomesite.com
Principal Broker

Miles Tandrow
801-555-0162
miles@harborlinehomesite.com
Real Estate Agent

Owen Tandrow
801-555-0138
owen@harborlinehomesite.com
Real Estate Agent

Harborline Realty & Investment Corp.
HarborlineHomesite.com
5286 N 7200 Suite 208-617, Cedar Bluff, ID 83799

Please feel free to reach out with any questions, comments, or concerns.

```html
<!DOCTYPE html>
<html lang="en">
<head>
<meta charset="utf-8">
<title>Harborline Realty – Business Card</title>
<link href="https://fonts.googleapis.com/css2?family=Montserrat:wght@500;600;700;800&family=Arimo:wght@400;700&display=swap" rel="stylesheet">
<style>
  :root {
    --bg: #262626;
    --card-grey: #6d6d6d;
    --card-grey-dark: #636363;
    --brand-blue: #38a9f5;
    --white: #ffffff;
    --ink: #111111;
    --photo-hair: #8a5a32;
    --photo-shirt: #e9e6e2;
  }
  * { box-sizing: border-box; margin: 0; padding: 0; }
  html, body { width: 1200px; height: 1015px; overflow: hidden; }
  body {
    background: var(--bg);
    display: flex;
    flex-direction: column;
    align-items: center;
    justify-content: center;
    gap: 56px;
    font-family: "Arimo", Arial, sans-serif;
  }
  .card {
    position: relative;
    width: 760px;
    height: 434px;
    overflow: hidden;
    background: var(--card-grey);
    box-shadow: 0 14px 30px rgba(0,0,0,.55);
  }

  /* Back */
  .card-back .seal {
    position: absolute;
    left: 430px; top: 20px;
    width: 300px; height: 300px;
    border-radius: 50%;
    border: 12px solid var(--card-grey-dark);
  }
  .card-back .wordmark {
    position: absolute;
    left: 40px; bottom: 40px;
  }

  .wordmark {
    font-family: "Montserrat", sans-serif;
    font-weight: 600;
    color: var(--white);
    line-height: 1;
    white-space: nowrap;
  }
  .wordmark .name { display: block; font-size: 40px; letter-spacing: 2px; }
  .wordmark .sub { display: block; font-size: 13px; letter-spacing: 5px; margin: 6px 0 0 62px; }

  /* Front */
  .photo {
    position: absolute;
    left: 44px; top: 30px;
    width: 240px; height: 240px;
    background: linear-gradient(180deg, var(--photo-hair) 0%, #b98b6a 45%, var(--photo-shirt) 78%);
    border-radius: 120px 120px 0 0;
  }
  .brand {
    position: absolute;
    left: 310px; top: 80px;
    display: flex;
    align-items: center;
    gap: 14px;
  }
  .brand .dot {
    width: 72px; height: 72px;
    border-radius: 50%;
    border: 7px solid var(--brand-blue);
    flex: none;
  }
  .brand .wordmark .name { font-size: 26px; letter-spacing: 1.5px; }
  .brand .wordmark .sub { font-size: 9px; letter-spacing: 3.5px; margin: 5px 0 0 42px; }

  .band {
    position: absolute;
    left: 0; top: 270px;
    width: 100%; height: 90px;
    background: var(--brand-blue);
    display: flex;
    align-items: center;
    color: var(--white);
  }
  .agent { width: 390px; text-align: right; padding-right: 26px; white-space: nowrap; }
  .agent-name { font-family: "Montserrat", sans-serif; font-weight: 800; font-size: 30px; letter-spacing: .5px; }
  .agent-role { font-size: 21px; margin-top: 2px; }
  .divider { width: 2px; height: 62px; background: var(--white); }
  .contact { list-style: none; padding-left: 22px; font-size: 17px; line-height: 24px; white-space: nowrap; }
  .contact li { display: flex; align-items: center; gap: 10px; }
  .contact svg { width: 16px; height: 16px; flex: none; }

  .address-strip {
    position: absolute;
    left: 0; top: 360px;
    width: 100%; height: 42px;
    background: var(--white);
    color: var(--ink);
    font-size: 21px;
    white-space: nowrap;
    display: flex; align-items: center; justify-content: center;
  }
  .footer-bar {
    position: absolute;
    left: 0; top: 402px;
    width: 100%; height: 32px;
    display: flex;
  }
  .footer-bar .blue { flex: 0 0 62%; background: var(--brand-blue); }
  .footer-bar .grey { flex: 1; background: var(--card-grey); }
</style>
</head>
<body>

  <section class="card card-back" aria-label="Card back">
    <div class="seal"></div>
    <div class="wordmark">
      <span class="name">HARBORLINE REALTY</span>
      <span class="sub">&amp; INVESTMENT CORP.</span>
    </div>
  </section>

  <section class="card card-front" aria-label="Card front">
    <div class="photo" role="img" aria-label="Headshot of Owen Tandrow"></div>

    <div class="brand">
      <span class="dot"></span>
      <div class="wordmark">
        <span class="name">HARBORLINE REALTY</span>
        <span class="sub">&amp; INVESTMENT CORP.</span>
      </div>
    </div>

    <div class="band">
      <div class="agent">
        <div class="agent-name">OWEN TANDROW</div>
        <div class="agent-role">Real Estate Agent</div>
      </div>
      <div class="divider"></div>
      <ul class="contact">
        <li>
          <svg viewBox="0 0 24 24" fill="none" stroke="#fff" stroke-width="2.4" stroke-linecap="round" stroke-linejoin="round"><path d="M5 3h4l2 5-2.5 1.5a11 11 0 0 0 6 6L16 13l5 2v4a2 2 0 0 1-2 2A17 17 0 0 1 3 5a2 2 0 0 1 2-2z"/></svg>
          801-555-0138
        </li>
        <li>
          <svg viewBox="0 0 24 24" fill="none" stroke="#fff" stroke-width="2.4" stroke-linejoin="round"><rect x="2" y="5" width="20" height="14"/><path d="M2 5l10 8 10-8"/></svg>
          owen@harborlinehomesite.com
        </li>
        <li>
          <svg viewBox="0 0 24 24" fill="none" stroke="#fff" stroke-width="2"><circle cx="12" cy="12" r="10"/><ellipse cx="12" cy="12" rx="4.5" ry="10"/><path d="M2 12h20M4 7h16M4 17h16"/></svg>
          www.HarborlineHomesite.com
        </li>
      </ul>
    </div>

    <div class="address-strip">5286 N 7200 Suite 208-617, Cedar Bluff, ID 83799</div>

    <div class="footer-bar"><span class="blue"></span><span class="grey"></span></div>
  </section>

</body>
</html>
```